Professional, modern and unique business card. We are looking to present a new look to our business cards however we don't want to divert too far away from original template. We want social media links and our 3 office addresses on the backside of the business cards. Please see attached business card templates for ideas.
Crestline Homes Color Code:
R: 7
G:63
B:86

Target Market(s)

Real Estate

Industry/Entity Type

Real Estate

Contact Information for Business Card

Follow the attached templates. In need of a more modern and unique touch but don't want to divert from the original theme or color.
Crestline Homes Color Code:
R: 7
G:63
B:86

Font styles to use
Serif

Requirements
Must have
• Crestline Homes logo, Crestline homes colors, social media links, 3 office addresses,
Nice to have
• information about Crestline Homes and QR codes. You can check out www.mycrestlinehomes.example

```html
<!DOCTYPE html>
<html lang="en">
<head>
<meta charset="utf-8">
<title>Crestline Homes – Business Card</title>
<link href="https://fonts.googleapis.com/css2?family=Marcellus&family=Lato:wght@400&display=swap" rel="stylesheet">
<style>
  :root {
    --bg: #2b2b2d;
    --card: #073f56;
    --band: #c9e8f3;
    --ink: #dbe9ef;
    --ink-soft: #b9ccd5;
    --dot-a: #3b5998;
    --dot-b: #c8232c;
    --dot-c: #d94a4a;
    --dot-d: #1f78b4;
    --dot-e: #3f6fa8;
    --dot-f: #2aa3e0;
  }
  * { margin: 0; padding: 0; box-sizing: border-box; }
  html, body { width: 1200px; height: 900px; overflow: hidden; background: var(--bg); }
  body { position: relative; font-family: "Lato", sans-serif; color: var(--ink); }

  .card {
    position: absolute; left: 320px; width: 560px; height: 320px;
    background: var(--card); overflow: hidden;
    box-shadow: 0 6px 18px rgba(0,0,0,.45);
  }
  .card::after {
    content: ""; position: absolute; left: 0; right: 0; bottom: 0; height: 9px; background: var(--band);
  }
  .card--front { top: 100px; }
  .card--back { top: 470px; }

  /* front */
  .brand {
    position: absolute; top: 96px; left: 0; right: 0;
    display: flex; align-items: center; justify-content: center; gap: 14px;
  }
  .brand__dot { width: 20px; height: 20px; border-radius: 50%; background: var(--ink); }
  .brand__name {
    font-family: "Marcellus", serif; font-size: 42px; color: var(--ink); letter-spacing: 1px;
  }
  .socials {
    position: absolute; left: 24px; right: 20px; bottom: 30px;
    display: grid; grid-template-columns: auto auto auto; justify-content: space-between;
    column-gap: 12px; row-gap: 8px;
    font-size: 13px;
  }
  .social { display: flex; align-items: center; gap: 6px; white-space: nowrap; }
  .social__dot { width: 16px; height: 16px; border-radius: 50%; flex: none; }
  .social:nth-child(1) .social__dot { background: var(--dot-a); }
  .social:nth-child(2) .social__dot { background: var(--dot-c); }
  .social:nth-child(3) .social__dot { background: var(--dot-e); }
  .social:nth-child(4) .social__dot { background: var(--dot-b); }
  .social:nth-child(5) .social__dot { background: var(--dot-d); }
  .social:nth-child(6) .social__dot { background: var(--dot-f); }

  /* back */
  .person { position: absolute; left: 40px; top: 110px; }
  .person__name { font-family: "Marcellus", serif; font-size: 22px; letter-spacing: 1px; color: var(--ink); }
  .person__title { font-size: 15px; letter-spacing: .5px; color: var(--ink-soft); margin-top: 2px; }

  .contacts { position: absolute; left: 300px; top: 140px; list-style: none; font-size: 15px; line-height: 19px; }
  .contacts li { display: flex; align-items: center; gap: 7px; }
  .contacts svg { width: 12px; height: 12px; fill: var(--ink); flex: none; }

  .offices {
    position: absolute; left: 14px; right: 14px; bottom: 26px;
    display: flex; font-size: 15px; line-height: 18px;
  }
  .office { padding: 0 14px; border-left: 1px solid var(--ink-soft); }
  .office:first-child { border-left: none; }
</style>
</head>
<body>

<section class="card card--front" aria-label="Business card front">
  <div class="brand">
    <span class="brand__name">Crestline Homes</span>
    <span class="brand__dot"></span>
  </div>
  <div class="socials">
    <div class="social"><span class="social__dot"></span>CrestlineHomesNY</div>
    <div class="social"><span class="social__dot"></span>Info at Crestline Homes</div>
    <div class="social"><span class="social__dot"></span>@CrestlineHomesNY</div>
    <div class="social"><span class="social__dot"></span>Crestline Homes</div>
    <div class="social"><span class="social__dot"></span>Crestline Homes New York</div>
    <div class="social"><span class="social__dot"></span>@CrestlineHomesQ</div>
  </div>
</section>

<section class="card card--back" aria-label="Business card back">
  <div class="person">
    <div class="person__name">DANA WHITFIELD</div>
    <div class="person__title">MANAGING DIRECTOR</div>
  </div>

  <ul class="contacts">
    <li><svg viewBox="0 0 12 12"><path d="M2 1h2l1 3-1.5 1a7 7 0 0 0 3.5 3.5L8 7l3 1v2a1 1 0 0 1-1 1A9 9 0 0 1 1 2a1 1 0 0 1 1-1z"/></svg>212 555 0147</li>
    <li><svg viewBox="0 0 12 12"><path d="M3 0h6v12H3zM4 1.5v8h4v-8z"/></svg>917 555 0182</li>
    <li><svg viewBox="0 0 12 12"><path d="M3 0h6v3H3zM1 4h10v5H9v3H3V9H1zM4 8v3h4V8z"/></svg>718 555 0126</li>
    <li><svg viewBox="0 0 12 12"><path d="M0 2h12v8H0zM1 3v.5l5 3.5 5-3.5V3z"/></svg>info@crestlinehomes.example</li>
    <li><svg viewBox="0 0 12 12"><circle cx="6" cy="6" r="5.5"/></svg>www.mycrestlinehomes.example</li>
  </ul>

  <div class="offices">
    <div class="office">140-08 Harbor Blvd<br>Bayside, NY 11360</div>
    <div class="office">72-30 Orchard Blvd<br>Forest Hills, NY 11375</div>
    <div class="office">1450 Maple Ave<br>Brooklyn, NY 11207</div>
  </div>
</section>

</body>
</html>
```